Modern Business Card for Larkwell 2018

Our company assumes the best about people. We are creating an online community of entrepreneurs and business leaders who struggle with marketing their business online.

This business card should POP! We recently got a new logo and are launching a new website next month, so our business cards should make a statement that feels:
-Fresh
-Smart
-Trustworthy
-Fun

Target Market(s)

small business owners, entrepreneurs

Industry/Entity Type

Digital Marketing

Contact Information for Business Card

Dimensions: 3.5" x 2"

Font styles to use
Sans Serif

Colors
f37122
ffffff

Requirements
Must have
• We need a business card with a modern, bold design. We will use one side of the card as a lead-generation offer, so text on one side will need to fit up to 140 characters. The business card should stick to our core colors (orange, black, and white).
Nice to have
• We think a vertical "portrait" design could be interesting.
Should not have
• Should not look like a traditional business card. The round icon should stand out from a distance.

```html
<!DOCTYPE html>
<html lang="en">
<head>
<meta charset="utf-8">
<title>Larkwell Business Card</title>
<link href="https://fonts.googleapis.com/css2?family=Roboto:wght@400;500;700;900&display=swap" rel="stylesheet">
<style>
  :root {
    --orange: #f37122;
    --white: #ffffff;
    --black: #1d1d1d;
    --grey: #6a6a6a;
    --blush: #fae4d8;
    --backdrop: #ece8e3;
  }
  * { box-sizing: border-box; margin: 0; padding: 0; }
  html, body { width: 1200px; height: 911px; overflow: hidden; }
  body {
    background: var(--backdrop);
    font-family: "Roboto", Arial, sans-serif;
    position: relative;
  }
  .card {
    position: absolute;
    top: 105px;
    width: 400px;
    height: 700px;
    border-radius: 4px;
    box-shadow: 0 10px 30px rgba(0,0,0,0.18);
    overflow: hidden;
  }
  /* Front */
  .card-front { left: 150px; background: var(--white); }
  .front-watermark {
    position: absolute;
    left: 60px; top: 70px;
    width: 300px; height: 300px;
    border-radius: 50%;
    background: var(--blush);
  }
  .front-brand {
    position: absolute;
    left: 48px; top: 420px;
    display: flex; align-items: center; gap: 12px;
  }
  .brand-dot {
    width: 26px; height: 26px; border-radius: 50%;
    background: var(--orange);
  }
  .brand-name {
    font-weight: 900;
    font-size: 44px;
    letter-spacing: 2px;
    color: var(--black);
    text-transform: uppercase;
  }
  .front-tagline {
    position: absolute;
    left: 50px; top: 478px;
    font-size: 13px; font-weight: 700;
    letter-spacing: 2.5px;
    text-transform: uppercase;
    color: var(--black);
  }
  .edge-mark {
    position: absolute;
    left: 0; top: 540px;
    width: 14px; height: 46px;
    background: var(--orange);
  }
  .contact { position: absolute; left: 50px; top: 534px; }
  .contact-name {
    font-size: 28px; font-weight: 500;
    color: var(--orange); text-transform: uppercase;
  }
  .contact-title {
    font-size: 18px; font-weight: 500;
    color: var(--black); text-transform: uppercase;
    letter-spacing: 1px; margin-top: 6px;
  }
  .contact-email {
    font-size: 17px; color: var(--grey); margin-top: 6px;
  }
  /* Back */
  .card-back { left: 650px; background: var(--orange); color: var(--white); }
  .back-mark {
    position: absolute;
    left: 50%; top: 70px;
    width: 170px; height: 170px;
    margin-left: -85px;
    border-radius: 50%;
    background: var(--white);
  }
  .back-copy { position: absolute; left: 40px; right: 40px; top: 300px; text-align: center; }
  .offer-headline {
    font-weight: 900; font-size: 25px; line-height: 1.15;
    text-transform: uppercase;
  }
  .offer-body { font-size: 18px; line-height: 1.35; margin-top: 14px; }
  .offer-url { font-size: 22px; font-weight: 900; margin-top: 14px; }
  .notes-box {
    position: absolute;
    left: 30px; right: 30px; bottom: 40px;
    height: 130px;
    background: var(--white);
    border-radius: 14px;
    padding: 40px 20px 0;
  }
  .notes-line { height: 1px; background: #555; margin-bottom: 40px; }
</style>
</head>
<body>
  <section class="card card-front" aria-label="Card front">
    <div class="front-watermark" role="img" aria-label="Large faint brand circle"></div>
    <div class="front-brand">
      <span class="brand-dot"></span>
      <span class="brand-name">Larkwell</span>
    </div>
    <p class="front-tagline">Tell stories that inspire action</p>
    <div class="edge-mark"></div>
    <div class="contact">
      <p class="contact-name">Dana Whitford</p>
      <p class="contact-title">Story Marketing Coach</p>
      <p class="contact-email">dana@larkwellnow.com</p>
    </div>
  </section>

  <section class="card card-back" aria-label="Card back">
    <div class="back-mark" role="img" aria-label="Brand circle"></div>
    <div class="back-copy">
      <p class="offer-headline">Reach more people.<br>Make more money.<br>Create more impact.</p>
      <p class="offer-body">Get your free Larkwell<br>Starter Package and our<br>marketing guide today at</p>
      <p class="offer-url">Larkwellnow.com/start</p>
    </div>
    <div class="notes-box">
      <div class="notes-line"></div>
      <div class="notes-line"></div>
    </div>
  </section>
</body>
</html>
```